Business card for Crestline Bathrooms

Please design a business card for our bathroom renovation business. You can use my existing logo, but if you have an idea to modernize it, I would like to see it. Please see attached files first. I would like to use the blue and the orange theme. I like the concept of using the shower head in the logo. Please find following a design (or two) that I have been trying to create with my limited resources. That design was for a sign, but I was going to adopt it and use it as a business card as well. I like the concept of the water splash but I don’t think it “flows” nicely together with the logo. Another thought is that maybe creating the logo out of water splash could work and have a dramatic effect (like the water text and the butterfly picture attached with similar background instead of white). If the above doesn’t work I would like to see a modern simplified design. One of the attached files named as the unwanted business card has all the details that I want included in the business card. Please note that it is two sided.
Updates

I am very thankful for the designs that I have received, but they are very similar and only a couple of attempts to do something with the water splash as per my original brief. Modernizing the logo and having it made out of out of water splash with the orange as color accent could work and have a dramatic effect (like the water text and the butterfly picture attached with similar background instead of white). Please do not use the butterfly itself! This is just an example that images can be created out of water splash.

Contact Information for Business Card

all the details are on the unwonted business card file included

Colors
3176b5

Requirements
Nice to have
• Copied from the brief:
• ... maybe creating the logo out of water splash could work and have a dramatic effect (like the water text and the butterfly picture attached with similar background instead of white). Please do not use the butterfly itself!
Should not have
• I am getting designs with a butterfly. The butterfly picture was an example of creating something from a water splash. The butterfly itself has no association with anything other than the concept of creating a logo out of water splash. Sorry, I thought I was clear in the brief.

```html
<!DOCTYPE html>
<html lang="en">
<head>
<meta charset="utf-8">
<title>Crestline Bathrooms – Business Card</title>
<link href="https://fonts.googleapis.com/css2?family=Arimo:wght@400;700&display=swap" rel="stylesheet">
<style>
  :root {
    --backdrop: #8e8e8e;
    --card-white: #f4f4f4;
    --navy: #0e3a66;
    --deep-blue: #054271;
    --coral: #ef7a6a;
    --text-dark: #2a2a2a;
    --badge-green: #2aa836;
    --badge-neutral: #d9dde3;
  }
  * { margin: 0; padding: 0; box-sizing: border-box; }
  html, body { width: 1200px; height: 1200px; overflow: hidden; }
  body {
    background: var(--backdrop);
    font-family: "Arimo", Arial, sans-serif;
    position: relative;
  }
  .card {
    position: absolute;
    top: 310px;
    height: 594px;
    box-shadow: 2px 3px 4px rgba(0,0,0,0.35);
  }
  .card-front {
    left: 234px; width: 364px;
    background: var(--card-white);
    text-align: center;
  }
  .card-back {
    left: 627px; width: 369px;
    background: var(--deep-blue);
    overflow: hidden;
  }

  /* Front */
  .brand {
    position: absolute;
    top: 116px; left: 34px; right: 30px;
    display: flex; align-items: center; gap: 14px;
  }
  .brand-square {
    width: 76px; height: 76px;
    border: 3px solid var(--navy);
    flex: none;
  }
  .brand-name {
    color: var(--navy);
    font-weight: 400;
    font-size: 30px;
    line-height: 1.05;
    text-align: left;
  }
  .person {
    position: absolute; top: 293px; left: 0; right: 0;
    font-size: 21px; font-weight: 700; letter-spacing: 0.2px;
    color: var(--navy);
  }
  .person .surname { color: var(--coral); }
  .dash-rule {
    position: absolute; left: 81px; width: 203px; height: 3px;
    background: repeating-linear-gradient(90deg,
      var(--coral) 0 10px, transparent 10px 16px,
      var(--navy) 16px 26px, transparent 26px 32px);
  }
  .dash-rule.top { top: 332px; }
  .dash-rule.bottom { top: 446px; }
  .contacts {
    position: absolute; top: 350px; left: 0; right: 0;
    list-style: none;
    font-size: 17px; line-height: 21.5px;
    color: var(--text-dark);
  }
  .contacts b { color: var(--navy); }
  .address {
    position: absolute; top: 468px; left: 0; right: 0;
    font-size: 17px; color: var(--text-dark);
  }
  .memberships {
    position: absolute; top: 508px; left: 66px;
    display: flex; align-items: center; gap: 12px;
  }
  .badge-trade {
    width: 46px; height: 56px; border-radius: 10px;
    background: var(--badge-green);
  }
  .badge-guild {
    width: 174px; height: 40px; border-radius: 4px;
    background: var(--badge-neutral);
  }

  /* Back */
  .services {
    position: absolute; top: 110px; left: 0; right: 0;
    list-style: none; text-align: center;
    color: #ffffff;
    font-size: 15.5px; line-height: 24.6px;
    letter-spacing: 0.2px;
  }
  .splash {
    position: absolute; left: 0; right: 0; top: 330px; bottom: 0;
    background:
      radial-gradient(ellipse 55% 30% at 52% 72%, rgba(210,230,245,0.85), rgba(120,165,205,0.5) 55%, rgba(5,66,113,0) 100%),
      linear-gradient(180deg, var(--deep-blue) 0%, #0d4f82 70%, #1d5f93 100%);
  }
</style>
</head>
<body>

<section class="card card-front" aria-label="Business card front">
  <div class="brand">
    <span class="brand-square" aria-hidden="true"></span>
    <span class="brand-name">Crestline<br>Bathrooms</span>
  </div>

  <h1 class="person">PETER <span class="surname">DALMONT</span></h1>
  <div class="dash-rule top" aria-hidden="true"></div>

  <ul class="contacts">
    <li><b>P:</b> 0400 555 218</li>
    <li><b>M:</b> 6200 4417</li>
    <li><b>E:</b> peter@crestlinebathrooms.com.au</li>
    <li><b>W:</b> crestlinebathrooms.com.au</li>
  </ul>
  <div class="dash-rule bottom" aria-hidden="true"></div>

  <p class="address">PO Box 48 Kellmore 2620</p>

  <div class="memberships" aria-label="Industry memberships">
    <div class="badge-trade" role="img" aria-label="Trade association membership badge"></div>
    <div class="badge-guild" role="img" aria-label="Builders association membership badge"></div>
  </div>
</section>

<section class="card card-back" aria-label="Business card back">
  <ul class="services">
    <li>COMPLETE BATHROOM</li>
    <li>RENOVATIONS &amp; REMODELLING</li>
    <li>HIGHLY SKILLED &amp; QUALIFIED</li>
    <li>TRADESPEOPLE</li>
    <li>PROFESSIONAL SERVICE FROM</li>
    <li>CONCEPT TO COMPLETION</li>
    <li>ALL WORK GUARANTEED</li>
  </ul>
  <div class="splash" role="img" aria-label="Photograph of a crown-shaped water splash on a reflective surface"></div>
</section>

</body>
</html>
```